Stationery Design Project

I need a design that is simple, clean and modern, in square style, bold font.
The majority of the design needs to be White and Black with a splash of Red colour.
I would like a design for business cards and letter heads with the following information.
Name, Title, Phone, Fax, Email, Website and company ABN number

Target Market(s)

25 to 65 years old real estate clients

Industry/Entity Type

Business

Requirements
Must have
• All designs must incorporate Company Logo, Name, Title, Phone, Fax, Email, Website and company ABN number

```html
<!DOCTYPE html>
<html lang="en">
<head>
<meta charset="utf-8">
<title>Ember Crest Real Estate – Business Card</title>
<link href="https://fonts.googleapis.com/css2?family=Open+Sans:wght@400;600;700&display=swap" rel="stylesheet">
<style>
  :root {
    --brand-red: #bb1e2d;
    --ink: #231f20;
    --paper: #ffffff;
    --stage: #e9e6e2;
    --muted: #3a3a3a;
    --divider: #666666;
  }
  * { box-sizing: border-box; margin: 0; padding: 0; }
  html, body { width: 1200px; height: 402px; overflow: hidden; }
  body {
    background: var(--stage);
    font-family: "Open Sans", Arial, sans-serif;
    position: relative;
  }
  .card {
    position: absolute;
    top: 52px;
    width: 510px;
    height: 292px;
    border-radius: 22px;
    overflow: hidden;
  }
  /* Front */
  .card-front { left: 64px; background: var(--paper); }
  .front-band {
    position: absolute; left: 0; top: 0; bottom: 0;
    width: 46px; background: var(--brand-red);
  }
  .front-rule {
    position: absolute; left: 51px; top: 0; bottom: 0;
    width: 3px; background: var(--ink);
  }
  .wordmark {
    position: absolute;
    font-weight: 700;
    line-height: 1;
  }
  .card-front .wordmark { left: 98px; top: 46px; color: var(--ink); }
  .wordmark-name { display: block; font-size: 34px; letter-spacing: 0.5px; }
  .wordmark-tag { display: block; font-size: 12px; letter-spacing: 9px; margin-top: 10px; }

  .holder {
    position: absolute; left: 96px; top: 164px;
    color: var(--brand-red);
    white-space: nowrap;
  }
  .holder-name { font-size: 16px; font-weight: 700; }
  .holder-title { font-size: 12px; font-weight: 400; margin-left: 5px; }

  .contacts {
    position: absolute; left: 96px; top: 216px;
    list-style: none; font-size: 13px; color: var(--muted);
    white-space: nowrap;
  }
  .contacts li { display: flex; align-items: center; height: 17.5px; }
  .contacts svg { width: 11px; height: 11px; margin-right: 6px; fill: var(--brand-red); flex: none; }
  .contact-divider {
    position: absolute; left: 266px; top: 238px;
    width: 1px; height: 42px; background: var(--divider);
  }
  .address {
    position: absolute; left: 288px; top: 248px;
    font-size: 12.5px; line-height: 19px; color: var(--muted);
    white-space: nowrap;
  }

  /* Back */
  .card-back { left: 635px; background: var(--brand-red); }
  .card-back .wordmark {
    left: 0; right: 0; top: 62px;
    text-align: center; color: var(--paper);
  }
  .card-back .wordmark-name { font-size: 44px; }
  .card-back .wordmark-tag { font-size: 14px; letter-spacing: 12px; margin-top: 14px; }
  .abn {
    position: absolute; left: 0; right: 0; top: 236px;
    text-align: center; font-size: 16px; color: var(--paper);
  }
</style>
</head>
<body>
  <section class="card card-front">
    <div class="front-band"></div>
    <div class="front-rule"></div>

    <div class="wordmark">
      <span class="wordmark-name">EMBER CREST</span>
      <span class="wordmark-tag">REAL ESTATE</span>
    </div>

    <p class="holder"><span class="holder-name">Your name,</span><span class="holder-title">Title</span></p>

    <ul class="contacts">
      <li>
        <svg viewBox="0 0 12 12" aria-hidden="true"><path d="M2.5 1l2 2.2-1 1.3c.8 1.6 1.9 2.7 3.5 3.5l1.3-1L10.5 9 9.3 10.8C5 10.4 1.6 7 1.2 2.7z"/></svg>
        123-456-7890
      </li>
      <li>
        <svg viewBox="0 0 12 12" aria-hidden="true"><rect x="3" y="1" width="6" height="3"/><rect x="1" y="4.5" width="10" height="5" rx="1"/><rect x="3" y="8" width="6" height="3"/></svg>
        123-456-7890
      </li>
      <li>
        <svg viewBox="0 0 12 12" aria-hidden="true"><path d="M1 3h10v6H1z M1 3l5 3.5L11 3" stroke="#fff" stroke-width=".8"/></svg>
        info@embercrest.com
      </li>
      <li>
        <svg viewBox="0 0 12 12" aria-hidden="true"><circle cx="6" cy="6" r="5"/><path d="M1 6h10M6 1v10" stroke="#fff" stroke-width=".7"/></svg>
        www.website.com
      </li>
    </ul>

    <div class="contact-divider"></div>
    <p class="address">Street Name, City Name<br>State, City Zip Code</p>
  </section>

  <section class="card card-back">
    <div class="wordmark">
      <span class="wordmark-name">EMBER CREST</span>
      <span class="wordmark-tag">REAL ESTATE</span>
    </div>
    <p class="abn">ABN;123456789</p>
  </section>
</body>
</html>
```